Postcard Design

A house cleaning business. Focus on time saving and stress free. Free estimates. Want it to state that we can make your home sparkle or shine. I have been using the colors purple and black in the logo which I will attach.

Reason: I need a few more days to decide on this. Thank you

Industry/Entity Type

House

Colors
886aae
6b449b

Requirements
Must have
• website www.maplecrestmaids.us
phone # 555-316-2984

```html
<!DOCTYPE html>
<html lang="en">
<head>
<meta charset="utf-8">
<title>Maple Crest Maids – Cleaning Postcard</title>
<link rel="stylesheet" href="https://fonts.googleapis.com/css2?family=Roboto+Condensed:wght@400;700&family=Montserrat:ital,wght@1,800&family=Arimo:wght@700&display=swap">
<style>
  :root {
    --purple-deep: #3f1670;
    --purple: #6b449b;
    --purple-light: #886aae;
    --purple-text: #7c5fa8;
    --gold: #ffc20e;
    --yellow: #fff200;
    --tag-yellow: #ffe01a;
    --red: #e2231a;
    --white: #ffffff;
    --page: #dcdcdc;
  }
  * { margin: 0; padding: 0; box-sizing: border-box; }
  html, body { width: 962px; height: 1200px; overflow: hidden; }
  body { background: var(--page); position: relative; }

  .postcard {
    position: absolute; left: 83px; top: 85px;
    width: 797px; height: 1032px; overflow: hidden;
    background: radial-gradient(ellipse at 20% 10%, var(--purple) 0%, #51227f 45%, var(--purple-deep) 100%);
  }
  .postcard > * { position: absolute; }

  .backdrop { left: 0; top: 0; width: 797px; height: 1032px; }

  .headline {
    left: 42px; top: 38px;
    font-family: "Roboto Condensed", "Arial Narrow", sans-serif;
    font-weight: 700; color: var(--gold);
    font-size: 98px; line-height: 88px; letter-spacing: -0.5px;
  }
  .headline .service {
    display: block; color: var(--white);
    font-size: 54px; line-height: 60px; margin-top: 6px;
  }

  .tagline {
    left: 42px; top: 303px; width: 520px;
    font-family: "Montserrat", Arial, sans-serif;
    font-style: italic; font-weight: 800;
    color: var(--tag-yellow); font-size: 25px; line-height: 31px;
  }

  .services {
    left: 50px; top: 482px; color: var(--white);
    font-family: "Roboto Condensed", "Arial Narrow", sans-serif;
  }
  .services h2 { font-size: 21px; font-weight: 700; margin-bottom: 10px; }
  .services ul { list-style: none; }
  .services li {
    font-size: 22px; line-height: 27px; margin-bottom: 8px;
    padding-left: 15px; position: relative;
  }
  .services li::before {
    content: ""; position: absolute; left: 0; top: 7px;
    border-left: 10px solid var(--gold);
    border-top: 7px solid transparent; border-bottom: 7px solid transparent;
  }

  .sparkle {
    left: 52px; top: 746px;
    font-family: "Montserrat", Arial, sans-serif;
    font-style: italic; font-weight: 800;
    color: var(--gold); font-size: 31px; line-height: 33px;
  }

  .photo {
    left: 322px; top: 185px; width: 475px; height: 640px;
    background: radial-gradient(ellipse at 70% 40%, rgba(255,255,255,0.35) 0%, rgba(52,92,190,0.55) 45%, rgba(255,255,255,0) 75%);
  }

  .ribbon { left: 0; top: 0; width: 797px; height: 260px; }
  .ribbon-text {
    left: 560px; top: 30px; width: 260px;
    transform: rotate(41deg); transform-origin: center;
    text-align: center; color: var(--red);
    font-family: "Roboto Condensed", "Arial Narrow", sans-serif;
    font-weight: 700; font-size: 27px; line-height: 27px;
  }

  .contact {
    left: 56px; top: 900px; text-align: center;
    font-family: "Arimo", Arial, sans-serif; font-weight: 700;
    color: var(--purple-text);
  }
  .contact .phone { font-size: 51px; line-height: 56px; letter-spacing: 1px; }
  .contact .line { font-size: 20px; line-height: 27px; }

  .brand {
    left: 500px; top: 905px; width: 260px; height: 100px;
    display: flex; align-items: center; justify-content: center; gap: 10px;
    font-family: "Roboto Condensed", "Arial Narrow", sans-serif;
    font-weight: 700; font-size: 26px; color: var(--purple);
  }
  .brand .mark { width: 16px; height: 16px; background: var(--purple); border-radius: 50%; }
</style>
</head>
<body>
  <main class="postcard">
    <svg class="backdrop" viewBox="0 0 797 1032" aria-hidden="true">
      <path d="M0 838 C150 812 300 850 460 842 C600 834 700 810 797 790 L797 1032 L0 1032 Z" fill="#886aae"/>
      <path d="M0 885 C160 880 300 862 450 850 C600 836 700 812 797 806 L797 1032 L0 1032 Z" fill="#ffffff"/>
    </svg>

    <div class="photo" role="img" aria-label="Photo of a smiling cleaner in a blue apron and yellow gloves holding a mop and cleaning supplies"></div>

    <h1 class="headline">LOW COST<br>STRESS FREE<span class="service">CLEANING SERVICE</span></h1>

    <p class="tagline">Maple Crest Maids cleaning company offers old fashion, high-quality home cleaning services.</p>

    <section class="services">
      <h2>OUR SERVICES:</h2>
      <ul>
        <li>Inital Through Home Cleaning</li>
        <li>General Residential House Cleaning</li>
        <li>Special Cleaning After Events</li>
        <li>Seasonal Super Cleaning</li>
        <li>Packages Consistently Through<br>Hassle Free</li>
      </ul>
    </section>

    <p class="sparkle">WE CAN MAKE YOUR<br>HOUSE SPARKLE!</p>

    <svg class="ribbon" viewBox="0 0 797 260" aria-hidden="true">
      <polygon points="525,0 679,0 797,108 797,248" fill="#fff200"/>
    </svg>
    <p class="ribbon-text">CALL<br>TODAY FOR A<br>FREE ESTIMATE!</p>

    <address class="contact" style="font-style:normal">
      <div class="phone">555-316-2984</div>
      <div class="line">www.maplecrestmaids.us</div>
      <div class="line">hello@maplecrestmaids.us</div>
    </address>

    <div class="brand"><span class="mark"></span>Maple Crest Maids</div>
  </main>
</body>
</html>
```